High-end construction company needs a business card design

We need a modern looking business card that draws people in, is memorable and looks so good people will want to sick it on their fridges.
On the first side what is needed are:
Logo
My name - Tomasz Brelwik
Title - Managing Director
Website - www.varkelt.co.uk
Email - tomasz@varkelt.co.uk
Telephone - 020 5194 6281
Mobile - 07845139072
On the back side was is needed is a list of all the services we provide:
-Kitchen Renovations
-Bathroom Renovations
-House Renovations
-Garage Conversions
-Extensions
-Loft Conversions
-Conservatories
-Carpentry
-Tiling
-Electrical
-Plumbing & Heating
-Bricklaying
-Landscaping
-Decorating
-Plastering
We would like the colours to be the same shades as on the logo with grey or black for the words.
Target Market(s)
Anyone who needs building work done
Contact Information for Business Card
This business card is for a construction company which strives to deliver excellent service and quality.
The look and feel of the card should represent this.
Requirements
Must have
- On the first side what is needed are:
Logo
My name - Tomasz Brelwik
Title - Managing Director
Website - www.varkelt.co.uk
Email - tomasz@varkelt.co.uk
Telephone - 020 5194 6281
Mobile - 07845139072
Nice to have
- Cool looking features

```html
<!DOCTYPE html>
<html lang="en">
<head>
<meta charset="utf-8">
<title>Varkelt Construction Ltd — Business Card</title>
<link rel="stylesheet" href="https://fonts.googleapis.com/css2?family=Montserrat:wght@400;600;700;800&family=Questrial&display=swap">
<style>
  :root {
    --bg: #d9d9d9;
    --green: #5bab41;
    --green-light: #7cc35a;
    --green-dark: #3d8a34;
    --green-deep: #2f7a30;
    --green-back-a: #2f7b2f;
    --green-back-b: #62a15d;
    --text-grey: #4a4a4a;
    --white: #ffffff;
  }
  * { margin: 0; padding: 0; box-sizing: border-box; }
  html, body { width: 1200px; height: 1200px; overflow: hidden; background: var(--bg); }
  .canvas { position: relative; width: 1200px; height: 1200px; }

  .card { position: absolute; left: 200px; width: 800px; height: 457px; overflow: hidden;
          box-shadow: 0 22px 30px rgba(0,0,0,0.28); }
  .card--front { top: 120px; background: var(--white); }
  .card--back { top: 640px; background: linear-gradient(225deg, var(--green-back-b) 0%, var(--green-back-a) 70%); }

  /* front */
  .front__artwork { position: absolute; left: 0; top: 0; width: 510px; height: 440px;
    background: radial-gradient(ellipse at 55% 55%, rgba(230,230,230,0.7) 0%, rgba(240,240,240,0.35) 50%, rgba(255,255,255,0) 75%); }
  .brand { position: absolute; right: 72px; top: 120px; display: flex; align-items: center; gap: 12px;
    color: var(--green); font-family: 'Montserrat', sans-serif; font-weight: 800; }
  .brand__mark { width: 22px; height: 22px; background: var(--green); }
  .brand__name { font-size: 46px; line-height: 1; letter-spacing: 1px; }
  .brand__sub { position: absolute; right: 72px; top: 176px; color: var(--green);
    font-family: 'Montserrat', sans-serif; font-weight: 800; font-size: 13.5px; letter-spacing: 2.6px; }

  .person { position: absolute; left: 55px; top: 252px; font-family: 'Montserrat', sans-serif; }
  .person__name { color: var(--green); font-size: 28px; font-weight: 700; letter-spacing: 0.5px; line-height: 1.1; }
  .person__title { color: var(--green-deep); font-size: 16px; font-weight: 600; margin-top: 3px; }
  .divider { position: absolute; left: 55px; top: 318px; width: 670px; height: 2px; background: var(--green-dark); }

  .contacts { position: absolute; left: 56px; top: 332px; list-style: none;
    font-family: 'Montserrat', sans-serif; font-size: 18px; color: var(--text-grey); }
  .contacts li { display: flex; align-items: center; height: 23px; }
  .contacts svg { width: 14px; height: 14px; margin-right: 9px; fill: var(--green-dark); }

  .front__band { position: absolute; left: 0; bottom: 0; width: 100%; height: 40px; }
  .website { position: absolute; right: 34px; bottom: 10px; color: var(--white);
    font-family: 'Montserrat', sans-serif; font-weight: 700; font-size: 17px; letter-spacing: 1.4px; }

  /* back */
  .back__artwork { position: absolute; left: 240px; top: 52px; width: 320px; height: 188px;
    background: linear-gradient(180deg, rgba(255,255,255,0.08) 0%, rgba(255,255,255,0.22) 100%); }
  .back__baseline { position: absolute; left: 172px; top: 243px; width: 434px; height: 3px; background: var(--white); }
  .services { position: absolute; left: 0; top: 270px; width: 100%; text-align: center;
    font-family: 'Questrial', sans-serif; font-size: 19px; color: var(--white); line-height: 25px; white-space: nowrap; }
  .services .tick { display: inline-block; width: 14px; height: 14px; vertical-align: -1px; margin: 0 4px 0 3px; }
  .social { position: absolute; top: 392px; left: 0; width: 100%; display: flex; justify-content: center; gap: 6px; }
  .social__item { width: 24px; height: 24px; border: 2px solid var(--white); border-radius: 6px; }
</style>
</head>
<body>
<div class="canvas">

  <section class="card card--front">
    <div class="front__artwork" role="img" aria-label="Faint excavator and buildings illustration"></div>

    <div class="brand"><span class="brand__mark"></span><span class="brand__name">VARKELT</span></div>
    <div class="brand__sub">CONSTRUCTION LTD</div>

    <div class="person">
      <div class="person__name">TOMASZ BRELWIK</div>
      <div class="person__title">MANAGING DIRECTOR</div>
    </div>
    <div class="divider"></div>

    <ul class="contacts">
      <li><svg viewBox="0 0 16 16"><path d="M3.5 1l3 3-1.8 1.8c.9 2 2.5 3.6 4.5 4.5L11 8.5l3 3-2 2.5C6.5 13.5 2.5 9.5 1 3.5z"/></svg>020 5194 6281</li>
      <li><svg viewBox="0 0 16 16"><path d="M4 0h8v16H4zM5.5 2v10h5V2zM7 13h2v1.5H7z" fill-rule="evenodd"/></svg>07845139072</li>
      <li><svg viewBox="0 0 16 16"><path d="M1 3h14v10H1zM2 4.5v.5l6 4 6-4v-.5z" fill-rule="evenodd"/></svg>tomasz@varkelt.co.uk</li>
    </ul>

    <svg class="front__band" viewBox="0 0 800 40" preserveAspectRatio="none">
      <rect x="0" y="23" width="540" height="17" fill="var(--green-dark)"/>
      <polygon points="526,40 544,23 548,23 531,40" fill="var(--white)"/>
      <polygon points="534,40 575,0 800,0 800,40" fill="var(--green-light)"/>
    </svg>
    <div class="website">www.varkelt.co.uk</div>
  </section>

  <section class="card card--back">
    <div class="back__artwork" role="img" aria-label="White excavator over house and buildings illustration"></div>
    <div class="back__baseline"></div>

    <div class="services">
      <div>Kitchen Renovations<svg class="tick" viewBox="0 0 14 14"><rect x="1" y="1" width="12" height="12" fill="none" stroke="#fff" stroke-width="1.6"/><path d="M3.5 7l2.5 2.5 4.5-5" fill="none" stroke="#fff" stroke-width="1.8"/></svg>Bathroom Renovations<svg class="tick" viewBox="0 0 14 14"><rect x="1" y="1" width="12" height="12" fill="none" stroke="#fff" stroke-width="1.6"/><path d="M3.5 7l2.5 2.5 4.5-5" fill="none" stroke="#fff" stroke-width="1.8"/></svg>House Renovations</div>
      <div>Garage Conversions<svg class="tick" viewBox="0 0 14 14"><rect x="1" y="1" width="12" height="12" fill="none" stroke="#fff" stroke-width="1.6"/><path d="M3.5 7l2.5 2.5 4.5-5" fill="none" stroke="#fff" stroke-width="1.8"/></svg>Extensions<svg class="tick" viewBox="0 0 14 14"><rect x="1" y="1" width="12" height="12" fill="none" stroke="#fff" stroke-width="1.6"/><path d="M3.5 7l2.5 2.5 4.5-5" fill="none" stroke="#fff" stroke-width="1.8"/></svg>Loft Conversions<svg class="tick" viewBox="0 0 14 14"><rect x="1" y="1" width="12" height="12" fill="none" stroke="#fff" stroke-width="1.6"/><path d="M3.5 7l2.5 2.5 4.5-5" fill="none" stroke="#fff" stroke-width="1.8"/></svg>Conservatories</div>
      <div>Carpentry<svg class="tick" viewBox="0 0 14 14"><rect x="1" y="1" width="12" height="12" fill="none" stroke="#fff" stroke-width="1.6"/><path d="M3.5 7l2.5 2.5 4.5-5" fill="none" stroke="#fff" stroke-width="1.8"/></svg>Tiling<svg class="tick" viewBox="0 0 14 14"><rect x="1" y="1" width="12" height="12" fill="none" stroke="#fff" stroke-width="1.6"/><path d="M3.5 7l2.5 2.5 4.5-5" fill="none" stroke="#fff" stroke-width="1.8"/></svg>Electrical<svg class="tick" viewBox="0 0 14 14"><rect x="1" y="1" width="12" height="12" fill="none" stroke="#fff" stroke-width="1.6"/><path d="M3.5 7l2.5 2.5 4.5-5" fill="none" stroke="#fff" stroke-width="1.8"/></svg>Plumbing &amp; Heating<svg class="tick" viewBox="0 0 14 14"><rect x="1" y="1" width="12" height="12" fill="none" stroke="#fff" stroke-width="1.6"/><path d="M3.5 7l2.5 2.5 4.5-5" fill="none" stroke="#fff" stroke-width="1.8"/></svg>Bricklaying</div>
      <div>Landscaping<svg class="tick" viewBox="0 0 14 14"><rect x="1" y="1" width="12" height="12" fill="none" stroke="#fff" stroke-width="1.6"/><path d="M3.5 7l2.5 2.5 4.5-5" fill="none" stroke="#fff" stroke-width="1.8"/></svg>Decorating<svg class="tick" viewBox="0 0 14 14"><rect x="1" y="1" width="12" height="12" fill="none" stroke="#fff" stroke-width="1.6"/><path d="M3.5 7l2.5 2.5 4.5-5" fill="none" stroke="#fff" stroke-width="1.8"/></svg>Plastering</div>
    </div>

    <div class="social">
      <span class="social__item"></span>
      <span class="social__item"></span>
      <span class="social__item"></span>
    </div>
  </section>

</div>
</body>
</html>
```